Post storm repair flyer

looking for an eye catching 6x9 postcard to send out to single family home owners advertising a "Post Storm Repair Special" explaining that after the recent hurricanes its very important to have your roof checked and any repairs fixed right away before they become a bigger more costly problem and that even though your home wasn't directly hit by the storm the high wind gust could've cause unseen damage.
offer $200 off any repair *some rules may apply
Crest Roofing
877.512.DUNE
www.DuneRoofingco.example

```html
<!DOCTYPE html>
<html lang="en">
<head>
<meta charset="utf-8">
<title>Crest Roofing – Post Storm Repair Special Postcard</title>
<link href="https://fonts.googleapis.com/css2?family=Lato:wght@400;700;900&display=swap" rel="stylesheet">
<style>
  :root {
    --gold: #f6ae00;
    --gold-soft: #e9b43a;
    --ink: #111111;
    --paper: #ffffff;
    --stage: #c9c9c9;
    --roof-dark: #4a4f58;
    --roof-mid: #7b808a;
    --sky: #c7ccd3;
    --grey-photo: #d8d8d8;
  }
  * { margin: 0; padding: 0; box-sizing: border-box; }
  html, body { width: 1200px; height: 2946px; overflow: hidden; }
  body {
    background: var(--stage);
    font-family: "Lato", Arial, sans-serif;
    color: var(--ink);
    position: relative;
  }
  .postcard {
    position: absolute;
    left: 92px;
    width: 1016px;
    height: 718px;
    background: var(--paper);
    overflow: hidden;
    box-shadow: 0 18px 30px rgba(0,0,0,.28);
  }
  .postcard--front { top: 560px; }
  .postcard--back { top: 1720px; }
  .postcard__art { position: absolute; inset: 0; width: 1016px; height: 718px; }
  .abs { position: absolute; }

  /* brand lockup */
  .brand {
    display: flex; align-items: center; gap: 8px;
    font-weight: 700; font-size: 15px; letter-spacing: .5px;
    text-transform: uppercase; color: var(--ink); white-space: nowrap;
  }
  .brand__mark { width: 14px; height: 14px; background: var(--ink); }

  /* front */
  .front-brand { left: 52px; top: 98px; }
  .tag-post {
    left: 51px; top: 143px; width: 126px; height: 40px;
    background: var(--gold);
    clip-path: polygon(0 0, 82% 0, 100% 100%, 0 100%);
    font-weight: 900; font-size: 36px; line-height: 40px; padding-left: 6px;
  }
  .headline-storm { left: 48px; top: 178px; font-weight: 900; font-size: 82px; line-height: 82px; letter-spacing: -1px; }
  .headline-repair { left: 51px; top: 256px; font-weight: 900; font-size: 43px; line-height: 44px; white-space: nowrap; }
  .headline-repair span { color: var(--gold); }
  .headline-rule { left: 51px; top: 302px; width: 361px; height: 3px; background: var(--ink); }
  .lead { left: 52px; top: 316px; font-weight: 700; font-size: 17px; line-height: 20px; }
  .fine { left: 52px; top: 360px; width: 340px; font-size: 11px; line-height: 13px; }
  .offer-bar { left: 32px; top: 423px; width: 10px; height: 126px; background: var(--gold-soft); }
  .offer { left: 52px; top: 418px; font-weight: 900; font-size: 50px; line-height: 45px; white-space: nowrap; }
  .offer .offer__accent { color: var(--gold); font-weight: 700; }
  .call-pill {
    background: var(--ink); color: var(--gold);
    font-weight: 900; font-size: 27px; line-height: 38px;
    border-radius: 0 22px 22px 0; padding: 0 24px 0 42px; white-space: nowrap;
  }
  .front-call { left: 0; top: 585px; }
  .phone { font-weight: 900; font-size: 50px; line-height: 52px; letter-spacing: -.5px; white-space: nowrap; }
  .web { font-weight: 900; font-size: 18px; letter-spacing: 1px; white-space: nowrap; }
  .front-phone { left: 40px; top: 628px; }
  .front-web { left: 45px; top: 680px; }

  /* back */
  .process-title { left: 51px; top: 64px; font-weight: 900; font-size: 45px; line-height: 44px; white-space: nowrap; }
  .steps { left: 51px; top: 208px; width: 450px; list-style: none; }
  .step { position: relative; padding-left: 34px; font-size: 22px; line-height: 27px; margin-bottom: 37px; }
  .step strong { font-weight: 900; }
  .step__num {
    position: absolute; left: 0; top: 0; width: 18px; height: 82px;
    background: var(--ink); color: var(--paper);
    font-size: 11px; line-height: 18px; text-align: center;
  }
  .back-call { left: 0; top: 562px; padding-left: 56px; }
  .back-phone { left: 52px; top: 610px; }
  .back-web { left: 57px; top: 664px; }
  .back-brand { left: 592px; top: 128px; }
  .postage {
    left: 852px; top: 55px; width: 111px; height: 82px;
    border: 1px solid #777; font-family: Arial, Helvetica, sans-serif;
    font-weight: 700; font-size: 12px; line-height: 15px; text-align: center; padding-top: 4px;
  }
  .address {
    left: 627px; top: 292px; width: 336px; height: 104px;
    border: 1.5px solid #444; font-size: 19px; line-height: 23px; padding: 28px 0 0 34px;
  }
  .social { left: 469px; top: 664px; display: flex; gap: 6px; }
  .social__dot { width: 22px; height: 22px; border: 2px solid var(--ink); border-radius: 50%; }
  .footer-rule { left: 562px; top: 674px; width: 454px; height: 2px; background: var(--ink); }
</style>
</head>
<body>

<!-- FRONT -->
<section class="postcard postcard--front" aria-label="Postcard front">
  <svg class="postcard__art" viewBox="0 0 1016 718">
    <defs>
      <linearGradient id="roofMain" x1="0" y1="0" x2="1" y2="1">
        <stop offset="0" stop-color="var(--sky)"/>
        <stop offset=".3" stop-color="var(--roof-mid)"/>
        <stop offset="1" stop-color="var(--roof-dark)"/>
      </linearGradient>
      <linearGradient id="roofSmall" x1="0" y1="0" x2="1" y2="1">
        <stop offset="0" stop-color="#8a8f98"/>
        <stop offset="1" stop-color="#3b3f46"/>
      </linearGradient>
    </defs>
    <polygon points="698,40 1016,40 1016,50 706,50 515,450 500,450" fill="var(--gold)"/>
    <polygon points="640,155 660,155 560,360 540,360" fill="var(--ink)"/>
    <polygon points="600,155 640,155 538,370 500,370" fill="var(--gold)"/>
    <polygon role="img" aria-label="Roofer repairing asphalt shingles on a roof" points="720,58 1016,58 1016,640 780,640 690,560 580,400 640,165 720,165" fill="url(#roofMain)"/>
    <polygon role="img" aria-label="Close-up of layered roof shingles" points="598,370 720,420 728,560 598,630 486,560 480,420" fill="url(#roofSmall)" stroke="var(--paper)" stroke-width="8"/>
    <polygon role="img" aria-label="Storm-damaged shingles with missing tabs" points="755,420 855,470 855,610 755,660 650,610 650,470" fill="#8f949c" stroke="var(--paper)" stroke-width="8"/>
    <polygon points="855,470 870,478 870,620 860,625" fill="var(--gold)"/>
    <circle cx="690" cy="662" r="6" fill="var(--gold)"/>
    <path d="M470,560 C440,600 440,660 500,670 C560,680 600,640 570,610 C540,585 520,640 560,660" fill="none" stroke="var(--ink)" stroke-width="1.5" stroke-dasharray="2 4"/>
    <polygon points="468,542 482,548 470,560" fill="var(--gold)"/>
    <polygon points="0,602 300,602 400,640 600,718 0,718" fill="var(--gold)"/>
    <polygon points="440,620 520,620 700,718 620,718" fill="var(--ink)"/>
    <polygon points="520,620 580,620 760,718 700,718" fill="var(--paper)"/>
    <polygon points="600,640 1016,640 1016,718 760,718" fill="var(--ink)"/>
    <polygon points="830,640 1016,640 1016,658 840,658" fill="var(--gold)"/>
  </svg>

  <div class="abs brand front-brand"><span class="brand__mark"></span>Crest Roofing</div>
  <div class="abs tag-post">POST</div>
  <h1 class="abs headline-storm">STORM</h1>
  <div class="abs headline-repair">REPAIR <span>SPECIAL</span></div>
  <div class="abs headline-rule"></div>
  <p class="abs lead">Protect Your Home with a Roof Inspection<br>After the Storm</p>
  <p class="abs fine">Don't wait until the damage is visible or more severe. A quick inspection now can save you from expensive repairs later on. Stay proactive and protect your home!</p>
  <div class="abs offer-bar"></div>
  <div class="abs offer">OFFER<br>$200 OFF<br><span class="offer__accent">ANY REPAIR</span></div>
  <div class="abs call-pill front-call">CALL US TODAY</div>
  <div class="abs phone front-phone">877.512.DUNE</div>
  <div class="abs web front-web">www.DuneRoofingco.example</div>
</section>

<!-- BACK -->
<section class="postcard postcard--back" aria-label="Postcard back">
  <svg class="postcard__art" viewBox="0 0 1016 718">
    <defs>
      <linearGradient id="greyPhoto" x1="0" y1="0" x2="0" y2="1">
        <stop offset="0" stop-color="var(--paper)"/>
        <stop offset="1" stop-color="var(--grey-photo)"/>
      </linearGradient>
    </defs>
    <rect role="img" aria-label="Faded greyscale photo of a roofer at work" x="420" y="420" width="596" height="298" fill="url(#greyPhoto)"/>
    <polygon points="0,0 470,0 592,357 470,718 0,718" fill="var(--gold-soft)"/>
    <polygon points="378,0 458,0 592,357 566,330" fill="var(--ink)"/>
    <polygon points="469,517 515,517 440,718 378,718" fill="var(--ink)"/>
  </svg>

  <h2 class="abs process-title">CREST ROOFING<br>PROCESS</h2>
  <ol class="abs steps">
    <li class="step"><span class="step__num">1</span>Complimentary consultation to access your roofing needs and review our honest recommendations.</li>
    <li class="step"><span class="step__num">2</span>Our team of professionals replace, restore, or repair your roof making the process as stress-free as possible.</li>
    <li class="step"><span class="step__num">3</span><strong>100% SATISFACTION</strong>, peace of mind, and continued professional coverage backed by CREST Protection*.</li>
  </ol>
  <div class="abs call-pill back-call">CALL US TODAY</div>
  <div class="abs phone back-phone">877.512.DUNE</div>
  <div class="abs web back-web">www.DuneRoofingco.example</div>

  <div class="abs brand back-brand"><span class="brand__mark"></span>Crest Roofing</div>
  <div class="abs postage">PRSRT STD<br>ECRWSS<br>U.S.POSTAGE<br>PAID<br>EDDM Retail</div>
  <div class="abs address">Local<br>Postal Customer</div>
  <div class="abs social" aria-hidden="true"><span class="social__dot"></span><span class="social__dot"></span><span class="social__dot"></span></div>
  <div class="abs footer-rule"></div>
</section>

</body>
</html>
```